New Webpage for High Class Expert Witness Services Company

We are looking for a minimalist design for a webpage that just has our logo and an entry form offer to connect with one of our Liaisons.
The entry form should just ask for Name, Email, Contact Info and Description of Project.

Company Name is: The Marlowe Crest Advisory Services

Number of Pages Required

1 page

```html
<!DOCTYPE html>
<html lang="en">
<head>
<meta charset="utf-8">
<title>The Marlowe Crest Advisory Services — Request Consultation</title>
<link rel="stylesheet" href="https://fonts.googleapis.com/css2?family=Cinzel:wght@400&family=Josefin+Sans:wght@300&family=Figtree:wght@300;400;700&display=swap">
<style>
  :root {
    --bg-dark: #0d0d0d;
    --bg-warm: #4b3f2c;
    --text-light: #f2f0ec;
    --text-muted: #b9b4ab;
    --gold: #7a6434;
    --gold-button: #6d5830;
    --field: #dcdcdc;
    --card-edge: rgba(255,255,255,0.22);
  }
  * { box-sizing: border-box; margin: 0; padding: 0; }
  html, body { width: 1200px; height: 675px; overflow: hidden; }
  body {
    position: relative;
    background:
      radial-gradient(ellipse 720px 560px at 940px 560px, rgba(92,76,50,0.95) 0%, rgba(60,50,34,0.6) 45%, rgba(13,13,13,0) 100%),
      var(--bg-dark);
    color: var(--text-light);
    font-family: "Figtree", sans-serif;
  }
  .brand {
    position: absolute; left: 54px; top: 128px;
    display: flex; align-items: center; gap: 12px;
  }
  .brand-mark { width: 30px; height: 30px; background: var(--text-muted); }
  .brand-name {
    font-family: "Cinzel", serif; font-weight: 400;
    font-size: 19px; line-height: 1.15; letter-spacing: 1px;
    color: var(--text-muted); width: 300px;
  }
  .headline {
    position: absolute; left: 49px; top: 248px;
    font-family: "Cinzel", serif; font-weight: 400;
    font-size: 46px; line-height: 48px; letter-spacing: 1.5px;
    color: #fff;
  }
  .subline {
    position: absolute; left: 47px; top: 366px;
    font-family: "Josefin Sans", sans-serif; font-weight: 300;
    font-size: 23px; letter-spacing: 1.2px; color: var(--text-light);
  }
  .assurances {
    position: absolute; left: 47px; top: 423px;
    display: flex; gap: 20px;
    font-size: 18px; font-weight: 300; color: var(--text-light);
  }
  .assurances strong { font-weight: 700; color: var(--gold); }
  .inquiry-card {
    position: absolute; left: 700px; top: 131px; width: 352px; height: 413px;
    border-radius: 24px;
    border: 1px solid var(--card-edge);
    background: linear-gradient(160deg, rgba(70,64,56,0.55), rgba(95,84,66,0.55));
  }
  .inquiry-title {
    text-align: center; margin-top: 21px;
    font-size: 24px; font-weight: 300; color: var(--text-light);
  }
  .inquiry-title b { font-weight: 700; color: var(--text-muted); }
  .title-rule {
    width: 171px; height: 1px; margin: 12px auto 0;
    background: linear-gradient(90deg, transparent, rgba(0,0,0,0.55), transparent);
  }
  .inquiry-form { margin: 12px 0 0 44px; width: 264px; }
  .field-label { display: block; font-size: 11.5px; color: var(--text-light); margin-bottom: 2px; }
  .field-input {
    display: block; width: 264px; height: 35px; border: none; border-radius: 2px;
    background: var(--field); margin-bottom: 11px;
  }
  .field-area { height: 86px; resize: none; }
  .submit-button {
    display: block; width: 264px; height: 34px; border: none; border-radius: 2px;
    background: var(--gold-button); color: #fff;
    font-family: "Figtree", sans-serif; font-size: 11.5px;
  }
</style>
</head>
<body>
  <header class="brand">
    <span class="brand-mark"></span>
    <span class="brand-name">The Marlowe Crest Advisory Services</span>
  </header>

  <h1 class="headline">Strategic Defense for<br>High Stakes Matters</h1>
  <p class="subline">Expert witness integration &amp; legal defense support</p>
  <p class="assurances">
    <span><strong>100%</strong> Confidential</span>
    <span><strong>24 hr</strong> Response guarantee</span>
  </p>

  <section class="inquiry-card">
    <h2 class="inquiry-title">Tell us about Your <b>Matter</b></h2>
    <div class="title-rule"></div>
    <form class="inquiry-form">
      <label class="field-label" for="name">Full Name</label>
      <input class="field-input" id="name" type="text">
      <label class="field-label" for="email">Email</label>
      <input class="field-input" id="email" type="email">
      <label class="field-label" for="phone">Contact Number</label>
      <input class="field-input" id="phone" type="tel">
      <label class="field-label" for="desc">Description of Project</label>
      <textarea class="field-input field-area" id="desc"></textarea>
      <button class="submit-button" type="button">Request Consultation</button>
    </form>
  </section>
</body>
</html>
```